Business card for a new cabinet shop company named Veloran Cabinets for high end cabinets

Design a business card, thinking dark rich green with colours to speak of high end luxury ie; cream, gold, black possibly

Mitchell Tarrowby
Director Craftsman
Email: info@veloranjoinery-example.com.au
Instagram : @veloran.cabinets

```html
<!DOCTYPE html>
<html lang="en">
<head>
<meta charset="utf-8">
<title>Veloran Cabinets — Business Card</title>
<link rel="stylesheet" href="https://fonts.googleapis.com/css2?family=Poppins:wght@300;400&display=swap">
<style>
  :root {
    --stone-deep: #06140e;
    --stone-mid: #0f2a1e;
    --stone-vein: #1d4332;
    --band-green: #123023;
    --band-green-light: #24503c;
    --gold-deep: #b9822a;
    --gold: #d9a53c;
    --gold-bright: #f6d77a;
    --brand-gold: #c9a45a;
    --cream: #f1e8d2;
  }
  html, body {
    margin: 0;
    padding: 0;
    width: 1200px;
    height: 686px;
    overflow: hidden;
    background: var(--stone-deep);
  }
  .card {
    position: relative;
    width: 1200px;
    height: 686px;
    overflow: hidden;
    font-family: "Poppins", sans-serif;
  }
  .marble-surface {
    position: absolute;
    inset: 0;
    background:
      radial-gradient(ellipse at 30% 25%, var(--stone-vein) 0%, transparent 45%),
      radial-gradient(ellipse at 75% 70%, var(--stone-mid) 0%, transparent 50%),
      linear-gradient(135deg, var(--stone-mid) 0%, var(--stone-deep) 55%, var(--stone-mid) 100%);
  }
  .corner-swoops {
    position: absolute;
    inset: 0;
    width: 1200px;
    height: 686px;
  }
  .brand-square {
    position: absolute;
    left: 262px;
    top: 250px;
    width: 184px;
    height: 184px;
    box-sizing: border-box;
    border: 6px solid var(--brand-gold);
  }
  .brand-name {
    position: absolute;
    left: 516px;
    top: 226px;
    margin: 0;
    color: var(--brand-gold);
    font-weight: 300;
    line-height: 1;
  }
  .brand-name .word-main {
    display: block;
    font-size: 122px;
    letter-spacing: 2px;
  }
  .brand-name .word-sub {
    display: block;
    margin-top: 10px;
    font-size: 56px;
    letter-spacing: 27px;
    text-transform: uppercase;
  }
  .contact-block {
    position: absolute;
    right: 64px;
    bottom: 52px;
    text-align: right;
    color: var(--cream);
    font-weight: 300;
    line-height: 1.5;
  }
  .contact-block .person-name {
    margin: 0;
    font-size: 26px;
    font-weight: 400;
  }
  .contact-block .person-role {
    margin: 0 0 10px;
    font-size: 14px;
    letter-spacing: 4px;
    text-transform: uppercase;
    color: var(--brand-gold);
  }
  .contact-block .contact-line {
    margin: 0;
    font-size: 16px;
  }
  .contact-block .contact-label {
    color: var(--brand-gold);
  }
</style>
</head>
<body>
  <div class="card">
    <div class="marble-surface" role="img" aria-label="Dark green marble stone texture with faint veins"></div>

    <svg class="corner-swoops" viewBox="0 0 1200 686" aria-hidden="true">
      <defs>
        <linearGradient id="goldSheen" x1="0" y1="0" x2="1" y2="1">
          <stop offset="0" stop-color="#b9822a"/>
          <stop offset="0.45" stop-color="#f6d77a"/>
          <stop offset="1" stop-color="#b9822a"/>
        </linearGradient>
        <linearGradient id="greenBand" x1="0" y1="0" x2="1" y2="1">
          <stop offset="0" stop-color="#24503c"/>
          <stop offset="1" stop-color="#123023"/>
        </linearGradient>
      </defs>

      <path d="M640 0 Q1010 20 1200 330 L1200 0 Z" fill="url(#goldSheen)"/>
      <path d="M700 0 Q1030 35 1200 300 L1200 0 Z" fill="url(#greenBand)"/>
      <path d="M880 0 Q1100 40 1200 220 L1200 0 Z" fill="url(#goldSheen)"/>
      <path d="M930 0 Q1120 50 1200 190 L1200 0 Z" fill="#123023"/>

      <path d="M0 180 Q40 580 810 686 L0 686 Z" fill="url(#greenBand)"/>
      <path d="M0 290 Q70 600 720 686 L0 686 Z" fill="url(#goldSheen)"/>
      <path d="M0 330 Q90 615 650 686 L0 686 Z" fill="#123023"/>
      <path d="M0 470 Q100 650 420 686 L0 686 Z" fill="url(#goldSheen)"/>
      <path d="M0 500 Q110 660 360 686 L0 686 Z" fill="#24503c"/>
    </svg>

    <div class="brand-square" aria-hidden="true"></div>
    <h1 class="brand-name">
      <span class="word-main">veloran</span>
      <span class="word-sub">Cabinets</span>
    </h1>

    <address class="contact-block" style="font-style: normal;">
      <p class="person-name">Mitchell Tarrowby</p>
      <p class="person-role">Director Craftsman</p>
      <p class="contact-line"><span class="contact-label">Email:</span> info@veloranjoinery-example.com.au</p>
      <p class="contact-line"><span class="contact-label">Instagram:</span> @veloran.cabinets</p>
    </address>
  </div>
</body>
</html>
```